Corporate Design für Hausverwalterin und Immobilienvermarktung
Zielgruppe
Hausverwalterin und Immobilienvermarktung
Aufgabenstellung
wir sind im Immobiliensektor unterwegs und das Design soll edel und hochwertig sein

```html
<!DOCTYPE html>
<html lang="de">
<head>
<meta charset="utf-8">
<title>Kaltern Immobilien – Visitenkarte</title>
<link rel="stylesheet" href="https://fonts.googleapis.com/css2?family=Tinos:wght@400;700&display=swap">
<style>
  :root {
    --page: #ffffff;
    --card: #13273d;
    --gold: #c9a640;
    --gold-light: #d8b54c;
    --ink-light: #f2f2f2;
    --shadow: rgba(0, 0, 0, 0.45);
  }
  * { margin: 0; padding: 0; box-sizing: border-box; }
  html, body {
    width: 1200px;
    height: 2438px;
    overflow: hidden;
    background: var(--page);
  }
  body {
    position: relative;
    font-family: "Tinos", "Times New Roman", serif;
  }
  .card {
    position: absolute;
    left: 181px;
    width: 839px;
    height: 556px;
    background: var(--card);
    box-shadow: 30px 40px 60px var(--shadow);
  }
  .card--front { top: 985px; }
  .card--back { top: 1695px; }

  .brand {
    position: absolute;
    top: 160px;
    left: 0;
    right: 0;
    text-align: center;
    color: var(--gold);
  }
  .brand__mark {
    display: block;
    width: 26px;
    height: 26px;
    margin: 0 auto 70px;
    background: var(--gold);
  }
  .brand__name {
    font-weight: 400;
    font-size: 72px;
    line-height: 1;
    letter-spacing: 0.5px;
  }
  .brand__tagline {
    margin-top: 10px;
    font-size: 28px;
    letter-spacing: 0.5px;
  }

  .back {
    position: absolute;
    top: 80px;
    left: 0;
    right: 0;
    text-align: center;
    color: var(--ink-light);
    font-size: 20.5px;
    line-height: 27px;
    text-transform: uppercase;
  }
  .back__headline { margin-bottom: 27px; }
  .back__intro { margin-bottom: 36px; }
  .services {
    list-style: none;
    text-align: left;
    padding-left: 62px;
    color: var(--gold-light);
    font-weight: 700;
    margin-bottom: 40px;
  }
  .services li::before {
    content: "•";
    display: inline-block;
    width: 18px;
  }
</style>
</head>
<body>
  <section class="card card--front" aria-label="Vorderseite">
    <div class="brand">
      <span class="brand__mark"></span>
      <p class="brand__name">Kaltern Immobilien</p>
      <p class="brand__tagline">VERWALTUNG &amp; VERMARKTUNG</p>
    </div>
  </section>

  <section class="card card--back" aria-label="Rückseite">
    <div class="back">
      <p class="back__headline">Ganzheitliche Immobilienbetreuung mit Strategie</p>
      <p class="back__intro">Als zertifizierte Hausverwalterin &amp; Immobilienmaklerin<br>gemäß § 34c GewO verbinde ich klassische<br>Verwaltung mit wertoptimierter Vermarktung:</p>
      <ul class="services">
        <li>Hausverwaltung: rechtssicher &amp; entlastend.</li>
        <li>Asset Management: strategische Ertragssteigerung.</li>
        <li>Verkauf: marktgerecht &amp; professionell.</li>
      </ul>
      <p class="back__contact">Kaltern Immobilien - Ihr Eigentum in zuverlässigen Händen.<br>Telefon: 0151 836 20 47<br>E-Mail: info@kaltern-immobilien.de<br>Webseite: www.kaltern-immobilien.de</p>
    </div>
  </section>
</body>
</html>
```